Bright bears day nursery qrp limited

we would like create a website that can be updated by us easily as we have regular changes to what we provide and need. we would like something that is classy but also appealing from a child's aspect. we would be looking to add our own logo and our kinderwatch logo both attached, if you guys can create it and we will work with the preferred choice to add all the text.
We would like the links to family pathways, kinderwatch report and our chatterbook feed on the front page

we are looking for a website for our childcare business we have 2 nurseries that we would like one website.
showing our opening hours, price list, policies etc as well as photos, description of our day, staff photos and their training accreditation's.

Target Market(s)

Families

Industry/Entity Type

Childcare

Number of Pages Required

5+ page

Font styles to use
Serif

Colors

Designer to choose colors to be used in the design.

Requirements
Must have
• links to social media and other websites, photographs, links to download registration forms etc, parents able to leave reviews. google maps link, job opportunities
Nice to have
• facilities to take payments

```html
<!DOCTYPE html>
<html lang="en">
<head>
<meta charset="utf-8">
<title>Bright Bears Day Nursery</title>
<link href="https://fonts.googleapis.com/css2?family=Raleway:wght@400;500;600;700;800&display=swap" rel="stylesheet">
<style>
:root{
  --blue:#2b4a8e;
  --blue-deep:#233f7c;
  --blue-soft:#3a5a9c;
  --green:#4ca847;
  --pink:#d5307e;
  --ink:#222;
  --muted:#777;
  --neutral:#eef0f3;
  --white:#fff;
}
*{box-sizing:border-box;margin:0;padding:0}
html,body{width:1200px;height:4157px;overflow:hidden}
body{font-family:"Raleway",sans-serif;color:var(--ink);background:var(--white);position:relative}
.abs{position:absolute}
a{color:inherit;text-decoration:none}

/* top bar */
.topbar{left:0;top:0;width:1200px;height:33px;background:var(--green);color:#fff;font-size:12px;font-weight:600;display:flex;align-items:center;padding:0 100px;gap:22px}
.topbar .dot{width:14px;height:14px;border-radius:50%;border:2px solid #fff;display:inline-block;margin-right:6px;vertical-align:-3px}
.topbar .phone{margin-left:auto}

/* nav */
.nav{top:33px;left:0;width:1200px;height:155px;background:#fff}
.nav ul{list-style:none;display:flex;gap:26px;position:absolute;top:44px;font-size:13px;font-weight:700;color:var(--blue)}
.nav .left{left:100px}
.nav .right{right:100px}
.brand{left:536px;top:58px;width:128px;height:128px;border-radius:50%;background:#fff;box-shadow:0 2px 8px rgba(0,0,0,.12);display:flex;align-items:center;justify-content:center;text-align:center;font-weight:800;font-size:16px;line-height:1.2;color:var(--pink);z-index:3;padding:14px}

/* hero */
.hero-photo{top:188px;left:0;width:1200px;height:450px;background:linear-gradient(100deg,#e9d8c2 0%,#cdb59a 35%,#7b8f5c 52%,#c9ad92 70%,#8a7a6c 100%)}

/* about band */
.about{top:623px;left:0;width:1200px;height:444px;background:var(--blue)}
.wave{position:absolute;left:0;width:1200px;height:26px}
.about-photo{left:0;top:20px;width:500px;height:424px;background:linear-gradient(135deg,#f3eee6,#d8c3a5 45%,#e7b9a6 70%,#c6a98a)}
.about-text{left:565px;top:52px;width:535px;color:#fff}
.about-text h2{font-size:25px;font-weight:800;letter-spacing:1px;margin-bottom:24px}
.about-text p{font-size:12.5px;line-height:1.75;margin-bottom:16px;color:#e6ebf5}
.btn-white{display:inline-block;background:#fff;color:var(--blue);font-size:13px;font-weight:700;padding:12px 26px;border-radius:4px;margin-top:10px}

/* pricing */
.section-title{position:absolute;left:0;width:1200px;text-align:center;font-size:25px;font-weight:800;letter-spacing:1px}
.pricing-title{top:1114px}
.price-card{background:#fff;box-shadow:0 2px 10px rgba(0,0,0,.12);text-align:center;overflow:hidden}
.price-card .head{height:118px;background:var(--pink);color:#fff;font-size:25px;font-weight:700;padding-top:30px;position:relative}
.price-card.featured .head{background:var(--green)}
.price-card .head svg{position:absolute;left:0;bottom:-1px;width:100%;height:24px}
.price-card .lead{font-size:17px;font-weight:700;margin:14px 0 18px;white-space:nowrap}
.price-card .cols{display:flex;justify-content:space-around;font-size:15px;font-weight:600;margin-bottom:20px}
.price-card .vals{display:flex;justify-content:space-around;font-size:15px;font-weight:600}
.price-card .vals small{display:block;font-size:10px;font-weight:600;line-height:1.2}
.price-card.featured .vals{color:var(--green)}
.btn{display:inline-block;color:#fff;font-size:12px;font-weight:700;padding:9px 24px;border-radius:3px;background:var(--pink);margin-top:18px}
.featured .btn{background:var(--green)}
.snail{left:955px;top:1497px;width:160px;height:110px;border-radius:12px;background:var(--neutral);z-index:2}

/* gallery */
.gallery{top:1574px;left:0;width:1200px;height:450px;background:var(--blue)}
.gallery .section-title{top:42px;color:#fff}
.g-circle{width:232px;height:232px;border-radius:50%;border:5px solid #fff;top:122px}

/* staff */
.staff-title{left:100px;top:2084px;font-size:25px;font-weight:800;letter-spacing:1px}
.staff-copy{left:100px;top:2138px;width:595px;font-size:12.5px;line-height:1.75;color:var(--muted)}
.diamond{transform:rotate(45deg);border-radius:22px;overflow:hidden;border:5px solid #fff;box-shadow:0 2px 8px rgba(0,0,0,.15)}
.diamond-small{width:137px;height:137px;top:2315px}
.diamond-big{left:767px;top:2112px;width:266px;height:266px}
.socials{display:flex;gap:5px;position:absolute;top:2376px}
.socials span{width:16px;height:16px;border-radius:3px;background:var(--pink)}

/* enquiry */
.enquiry{top:2535px;left:0;width:1200px;height:390px;background:var(--blue)}
.boy{left:20px;top:60px;width:240px;height:330px;border-radius:110px 110px 0 0;background:linear-gradient(180deg,#c58d63,#8d5d3e 40%,#b04a3a 100%)}
.sun{left:610px;top:50px;width:100px;height:90px;border-radius:8px;background:var(--blue-soft)}
.clouds{left:920px;top:30px;width:250px;height:330px;background:var(--blue-soft);border-radius:12px}
.enquiry h2{position:absolute;left:316px;top:104px;color:#fff;font-size:25px;font-weight:800;letter-spacing:1px}
.field{position:absolute;height:36px;width:366px;background:#fff;border-radius:3px;font-size:11px;color:#999;padding:11px 14px}
.send{position:absolute;left:316px;top:289px;width:366px;height:34px;background:var(--green);color:#fff;font-size:13px;font-weight:700;text-align:center;line-height:34px;border-radius:3px}

/* blog */
.blog-title{top:2958px}
.post{top:3029px;width:324px;height:302px;background:#fff;box-shadow:0 1px 6px rgba(0,0,0,.12);text-align:center}
.post .img{height:171px}
.post h3{font-size:17px;font-weight:700;margin:16px 0 8px}
.post .meta{font-size:11px;color:var(--muted);margin-bottom:8px}
.post .meta b{color:var(--blue)}
.post p{font-size:11.5px;color:var(--muted);margin-bottom:6px}
.post a{font-size:11.5px;color:var(--blue);text-decoration:underline}

/* partners */
.partners{top:3408px;left:0;width:1200px;height:95px;background:var(--blue)}
.partners .arrow{position:absolute;top:32px;color:#fff;font-size:26px;font-weight:700}
.partner{position:absolute;top:14px;width:188px;height:67px;background:#fff}
.partner i{position:absolute;left:24px;top:18px;width:140px;height:30px;background:#dfe3ea;border-radius:3px}

/* footer */
.footer{top:3503px;left:0;width:1200px;height:654px;background:var(--green);color:#fff}
.footer .brand{left:522px;top:49px;width:156px;height:156px;z-index:1;color:var(--pink)}
.footer-nav{position:absolute;top:260px;left:0;width:1200px;display:flex;justify-content:center;gap:24px;font-size:13px;font-weight:600}
.footer-nav span.sep{opacity:.7}
.badge{position:absolute;top:324px;height:78px;background:var(--blue-deep);border-radius:2px}
.fpost{position:absolute;left:452px;width:420px;height:89px}
.fpost .thumb{position:absolute;left:0;top:0;width:130px;height:89px;border:3px solid #fff;background:linear-gradient(135deg,#c08b5c,#6d8a4c)}
.fpost .txt{position:absolute;left:152px;top:6px;font-size:12.5px;line-height:1.55}
.fpost .txt b{font-size:13px}
.fpost .txt .acts{font-size:11px;opacity:.9}
.pathways-badge{position:absolute;left:887px;top:324px;width:213px;height:136px;background:#fff;border-radius:4px}
.pathways-badge i{position:absolute;left:26px;top:34px;width:161px;height:68px;background:#e9eef7;border-radius:4px}
.footer hr{position:absolute;left:100px;top:557px;width:1000px;border:0;border-top:1px solid rgba(255,255,255,.4)}
.copy{position:absolute;left:0;top:598px;width:1200px;text-align:center;font-size:12px}
</style>
</head>
<body>

<div class="abs topbar">
  <span><span class="dot"></span>Opening Hours</span>
  <span>Mon - Thu - 8.00 - 19.00</span>
  <span>Fri - 8.00 - 17.00</span>
  <span>Sat - Sun Closed</span>
  <span class="phone">&#9742;&nbsp; 0300 555 0142</span>
</div>

<header class="abs nav">
  <ul class="left"><li>HOME</li><li>SERVICES</li><li>TEAM</li><li>ABOUT</li><li>ACTIVITIES</li></ul>
  <ul class="right"><li>GALLERY</li><li>BLOG</li><li>PRICES</li><li>CONTACT</li><li>ELEMETS</li></ul>
</header>
<div class="abs brand">Bright Bears Day Nursery</div>

<div class="abs hero-photo" role="img" aria-label="Photo of a nursery teacher leading a group of children in a classroom"></div>

<section class="abs about">
  <svg class="wave" style="top:-25px" viewBox="0 0 1200 26" preserveAspectRatio="none" aria-hidden="true">
    <defs><pattern id="bumps" width="120" height="26" patternUnits="userSpaceOnUse"><path d="M0 26 L0 14 Q30 -2 60 12 Q90 24 120 14 L120 26 Z" fill="#2b4a8e"/></pattern></defs>
    <rect width="1200" height="26" fill="url(#bumps)"/>
  </svg>
  <div class="abs about-photo" role="img" aria-label="Photo of a carer and toddlers playing with a wooden dolls house"></div>
  <div class="abs about-text">
    <h2>THE BEST DAYCARE</h2>
    <p>Lorem ipsum dolor sit amet, consectetur adipiscing elit. Nam efficitur mi enim, in congue lectus rutrum sed. Interdum et malesuada fames ac ante ipsum primis in faucibus. Nunc tempor eros tortor, id interdum dolor ornare id. Duis efficitur, odio in maximus tincidunt, diam sapien rutrum dolor, id egestas eros metus eget risus. Etiam faucibus, lectus at congue ultricies, erat arcu consequat sapien, non ultricies orci leo sed velit.</p>
    <p>Etiam vitae lorem consectetur, pretium orci vitae, consectetur orci. Donec eu justo ac enim placerat pharetra.</p>
    <a class="btn-white">READ MORE &gt;&gt;</a>
  </div>
</section>

<h2 class="section-title pricing-title">OUR PRICING LIST</h2>

<div class="abs price-card" style="left:100px;top:1194px;width:241px;height:302px">
  <div class="head">£26 / Half day<svg viewBox="0 0 240 24" preserveAspectRatio="none"><path d="M0 24 L0 12 Q60 -4 120 12 Q180 26 240 10 L240 24 Z" fill="#fff"/></svg></div>
  <div class="lead">8am-1pm or 1pm-6pm</div>
  <div class="cols"><span>Under 2's</span><span>2-5's</span></div>
  <div class="vals"><span>£26</span><span>£25</span></div>
  <a class="btn">CONTACT US</a>
</div>
<div class="abs price-card featured" style="left:341px;top:1164px;width:266px;height:346px;z-index:1">
  <div class="head" style="height:110px">£40 / Full day<svg viewBox="0 0 240 24" preserveAspectRatio="none"><path d="M0 24 L0 12 Q60 -4 120 12 Q180 26 240 10 L240 24 Z" fill="#fff"/></svg></div>
  <div class="lead">Full day &nbsp; (7.30-6pm)</div>
  <div class="cols"><span>Under 2's</span><span>2-5's</span></div>
  <div class="vals"><span>£40</span><span>£38</span></div>
  <a class="btn">CONTACT US</a>
</div>
<div class="abs price-card" style="left:607px;top:1194px;width:238px;height:302px">
  <div class="head">£168 / Full day<svg viewBox="0 0 240 24" preserveAspectRatio="none"><path d="M0 24 L0 12 Q60 -4 120 12 Q180 26 240 10 L240 24 Z" fill="#fff"/></svg></div>
  <div class="lead" style="font-size:15px">Full timeMon - Fri7.30-6pm</div>
  <div class="cols"><span>Under 2's</span><span>2-5's</span></div>
  <div class="vals"><span>£168</span><span>£161<small>(funded children<br>in holidays)</small></span></div>
  <a class="btn" style="margin-top:8px">CONTACT US</a>
</div>
<div class="abs price-card" style="left:845px;top:1194px;width:255px;height:302px">
  <div class="head">£130 / Half day<svg viewBox="0 0 240 24" preserveAspectRatio="none"><path d="M0 24 L0 12 Q60 -4 120 12 Q180 26 240 10 L240 24 Z" fill="#fff"/></svg></div>
  <div class="lead" style="font-size:12px">Full timefunded children3+ years old</div>
  <div class="cols"><span>Under 2's</span><span>2-5's</span></div>
  <div class="vals"><span>xxxxx</span><span>£130<small>During term time</small></span></div>
  <a class="btn" style="margin-top:10px">CONTACT US</a>
</div>

<div class="abs snail" role="img" aria-label="Placeholder for a decorative illustration"></div>

<section class="abs gallery">
  <h2 class="section-title">OUR GALLERY</h2>
  <div class="abs g-circle" style="left:103px;background:linear-gradient(135deg,#d9a47a,#b6473a 60%,#e9c19c)" role="img" aria-label="Gallery photo of a carer playing with children"></div>
  <div class="abs g-circle" style="left:355px;background:linear-gradient(135deg,#e8dcc6,#c59467 55%,#7a9bc2)" role="img" aria-label="Gallery photo of a teacher with a child and a guitar"></div>
  <div class="abs g-circle" style="left:610px;background:linear-gradient(135deg,#c9b7a2,#a98a74 50%,#e6d2bf)" role="img" aria-label="Gallery photo of a child playing with toys"></div>
  <div class="abs g-circle" style="left:868px;background:linear-gradient(135deg,#f1d9a5,#d7513b 50%,#5b8fc5)" role="img" aria-label="Gallery photo of children in a colourful playroom"></div>
  <svg class="wave" style="bottom:-25px;transform:scaleY(-1)" viewBox="0 0 1200 26" preserveAspectRatio="none" aria-hidden="true">
    <rect width="1200" height="26" fill="url(#bumps)"/>
  </svg>
</section>

<h2 class="abs staff-title">MEET OUR QUALIFIED STAFF</h2>
<p class="abs staff-copy">Proin urna ipsum, tincidunt vitae lorem vel, mollis sollicitudin lectus. In ut lectus at tortor lacinia sagittis. Proin id massa non ex viverra aliquam nec vel augue. Nam et felis ut turpis placerat imperdiet. Sed a velit sed nisi luctus efficitur. Proin egestas rhoncus lacus dictum feugiat. Quisque et scelerisque elit.</p>
<div class="abs diamond diamond-small" style="left:140px;background:linear-gradient(135deg,#e3b58c,#b8514a 55%,#5ba05a)" role="img" aria-label="Staff photo of a carer with a child"></div>
<div class="abs diamond diamond-small" style="left:375px;background:linear-gradient(135deg,#d6a174,#4d9a4d 55%,#e3c2a1)" role="img" aria-label="Staff photo of a teacher with children"></div>
<div class="abs diamond diamond-small" style="left:597px;background:linear-gradient(135deg,#cfa27e,#c43d7a 50%,#f1d6b8)" role="img" aria-label="Staff photo of a carer reading to children"></div>
<div class="socials" style="left:183px"><span></span><span></span><span></span></div>
<div class="socials" style="left:418px"><span></span><span></span><span></span></div>
<div class="socials" style="left:640px"><span></span><span></span><span></span></div>
<div class="abs diamond diamond-big" style="background:linear-gradient(135deg,#dcc1a6,#f4efe9 45%,#8a6a55)" role="img" aria-label="Portrait photo of a nursery manager"></div>

<section class="abs enquiry">
  <svg class="wave" style="top:-55px;height:56px" viewBox="0 0 1200 56" preserveAspectRatio="none" aria-hidden="true">
    <path d="M0 56 L0 20 Q300 0 600 30 Q900 60 1200 6 L1200 56 Z" fill="#2b4a8e"/>
  </svg>
  <div class="abs boy" role="img" aria-label="Photo of a smiling boy pointing at the form"></div>
  <div class="abs sun" role="img" aria-label="Placeholder for a small decorative illustration"></div>
  <div class="abs clouds" role="img" aria-label="Placeholder for a decorative background illustration"></div>
  <h2>ENQUIRY FORM</h2>
  <div class="field" style="left:316px;top:153px">Name...</div>
  <div class="field" style="left:734px;top:153px">Email...</div>
  <div class="field" style="left:316px;top:219px">Phone Number...</div>
  <div class="field" style="left:734px;top:219px">Enquiry Message...</div>
  <div class="send">SEND NOW</div>
</section>

<h2 class="section-title blog-title">OUR BLOG</h2>
<article class="abs post" style="left:100px">
  <div class="img" style="background:linear-gradient(135deg,#f0c98c,#d2483d 50%,#6a9ed0)" role="img" aria-label="Blog photo of toddlers playing at a table"></div>
  <h3>Toddler Care</h3>
  <div class="meta"><b>&#9635;</b> June 20 &nbsp; <b>&#9679;</b> 81 comments</div>
  <p>Aliquam erat volutpat. Maecenas iaculis mollis</p>
  <a>Learn More...</a>
</article>
<article class="abs post" style="left:438px">
  <div class="img" style="background:linear-gradient(135deg,#e9dccc,#c98a5c 50%,#7aa35a)" role="img" aria-label="Blog photo of a teacher doing crafts with children"></div>
  <h3>Activity Calendar</h3>
  <div class="meta"><b>&#9635;</b> June 20 &nbsp; <b>&#9679;</b> 81 comments</div>
  <p>Aliquam erat volutpat. Maecenas iaculis mollis</p>
  <a>Learn More...</a>
</article>
<article class="abs post" style="left:776px">
  <div class="img" style="background:linear-gradient(135deg,#d8c6b4,#a57557 50%,#e5d3bf)" role="img" aria-label="Blog photo of children painting at a table"></div>
  <h3>Painting Class</h3>
  <div class="meta"><b>&#9635;</b> June 20 &nbsp; <b>&#9679;</b> 81 comments</div>
  <p>Aliquam erat volutpat. Maecenas iaculis mollis</p>
  <a>Learn More...</a>
</article>

<section class="abs partners" aria-label="Partners">
  <span class="arrow" style="left:50px">&#8249;</span>
  <div class="partner" style="left:100px"><i></i></div>
  <div class="partner" style="left:305px"><i></i></div>
  <div class="partner" style="left:507px"><i></i></div>
  <div class="partner" style="left:709px"><i></i></div>
  <div class="partner" style="left:914px"><i></i></div>
  <span class="arrow" style="left:1122px">&#8250;</span>
</section>

<footer class="abs footer">
  <div class="abs brand">Bright Bears Day Nursery</div>
  <nav class="footer-nav"><span>HOME</span><span class="sep">|</span><span>TEAM</span><span class="sep">|</span><span>GALLERY</span><span class="sep">|</span><span>SERVICES</span><span class="sep">|</span><span>ABOUT US</span><span class="sep">|</span><span>CONTACT US</span></nav>
  <div class="badge" style="left:100px;width:158px"></div>
  <div class="badge" style="left:269px;width:147px"></div>
  <div class="fpost" style="top:324px">
    <div class="thumb" role="img" aria-label="Photo of the nursery building"></div>
    <div class="txt"><b>Lorem ipsum</b><br>Aliquam erat volutpat. Vestibulum commodo<br><span class="acts">&#9829; Likes &nbsp; &#10150; Share &nbsp; &#9679; Comment</span></div>
  </div>
  <div class="fpost" style="top:432px">
    <div class="thumb" role="img" aria-label="Photo of the nursery garden"></div>
    <div class="txt"><b>Lorem ipsum</b><br>Aliquam erat volutpat. Vestibulum commodo<br><span class="acts">&#9829; Likes &nbsp; &#10150; Share &nbsp; &#9679; Comment</span></div>
  </div>
  <div class="pathways-badge"><i></i></div>
  <hr>
  <p class="copy">© 2017 Bright Bears Day Nursery All rights Reserved.</p>
</footer>

</body>
</html>
```